Trovanta Overview and Demo Presentation

Objective:
Create a bold, visually engaging PowerPoint deck to present Trovanta’s sales process and system demo to local movers, emphasizing ease of use, increased profitability, and operational efficiency.
Key Elements:
• Design: High-impact graphics with Trovanta branding, minimal text, and clean layouts.
• Content: Step-by-step sales process, key selling points, system demo walkthrough, and a compelling call-to-action.
• Live Demo: Showcase Trovanta’s platform, focusing on instant guaranteed pricing, streamlined booking, and support features.
Deliverables:
A dynamic presentation designed to educate and convert local movers into Trovanta partners, ensuring seamless flow and strong audience engagement.

Target Market(s)

Local Movers

Industry/Entity Type

Household Goods Moving

Font styles to use
Sans Serif

Colors
0054AA
0677BA
7BADD7
CADEEF
E8F1F8
FFC000
F8CF3A
FAE287
FDF2CF
FEFAEE

Requirements
Must have
• Project Brief: Trovanta Sales Process Presentation Objective: Create a bold, visually engaging PowerPoint deck to present Trovanta’s sales process and system demo to local movers, emphasizing ease of use, increased profitability, and operational efficiency. Key Elements: • Design: High-impact graphics with Trovanta branding, minimal text, and clean layouts. • Content: Step-by-step sales process, key selling points, system demo walkthrough, and a compelling call-to-action. • Live Demo: Showcase Trovanta’s platform, focusing on instant guaranteed pricing, streamlined booking, and support features. Deliverables: A dynamic presentation designed to educate and convert local movers into Trovanta partners, ensuring seamless flow and strong audience engagement.

```html
<!DOCTYPE html>
<html lang="en">
<head>
<meta charset="utf-8">
<title>Trovanta Overview Deck</title>
<link rel="stylesheet" href="https://fonts.googleapis.com/css2?family=Poppins:wght@400;500;600;700;800&display=swap">
<style>
:root{
  --blue:#1556d6;
  --blue-deep:#0054aa;
  --blue-mid:#0677ba;
  --blue-soft:#7badd7;
  --blue-pale:#e8f1f8;
  --yellow:#ffc000;
  --yellow-warm:#f8cf3a;
  --yellow-pale:#fdf2cf;
  --ink:#1b1b1b;
  --text:#3a3a3a;
  --stage:#b3b3b3;
  --white:#ffffff;
}
*{box-sizing:border-box;margin:0;padding:0}
html,body{width:1200px;height:364px;overflow:hidden;background:var(--stage);font-family:'Poppins',sans-serif;color:var(--text)}
.deck{position:relative;width:1200px;height:364px}
.slide{position:absolute;width:285px;height:160px;background:var(--white);overflow:hidden}
.slide p{line-height:1.45}
.c1{left:14px}.c2{left:309px}.c3{left:605px}.c4{left:900px}
.r1{top:14px}.r2{top:187px}
.abs{position:absolute}
.brand{position:absolute;display:flex;align-items:center;gap:3px;font-weight:600;color:var(--blue);font-size:9.5px;letter-spacing:.2px}
.brand .mark{width:6px;height:6px;background:var(--yellow)}
.slide .brand.top{right:8px;top:8px}
.head{position:absolute;left:9px;top:9px;font-weight:700;font-size:7.6px;line-height:1.3;letter-spacing:.2px;color:var(--ink)}
.head .hl{color:var(--yellow)}
.head .bl{color:var(--blue)}
.tab{position:absolute;left:0;top:10px;width:3px;height:7px;background:var(--yellow);clip-path:polygon(0 0,100% 50%,0 100%)}
.foot{position:absolute;left:9px;right:8px;bottom:7px;display:flex;justify-content:space-between;font-size:2.4px;color:var(--yellow)}
.bar{position:absolute;left:0;right:0;bottom:0;height:2.5px;background:var(--yellow)}
.photo{position:absolute}
.small{font-size:3.9px;color:var(--text)}

/* slide 1 */
.cover .photo{left:0;top:0;width:129px;height:160px;background:linear-gradient(160deg,#a99b8c,#7c6f64 45%,#c9c3bb 70%,#8a8a8a)}
.cover .rule{position:absolute;left:129px;top:0;width:2px;height:160px;background:var(--yellow)}
.cover .bg{position:absolute;left:131px;top:0;right:0;bottom:0;background:linear-gradient(135deg,#f6f6f6,#e9e9e9 50%,#f4f4f4)}
.cover .brand{left:155px;top:47px;font-size:11.5px}
.cover .brand .mark{width:7px;height:7px}
.cover h1{position:absolute;left:153px;top:66px;font-size:10.4px;font-weight:700;color:var(--blue);line-height:1.3;letter-spacing:.3px}
.cover .tag{position:absolute;left:156px;top:103px;width:120px;font-size:5px;color:var(--text);line-height:1.6}

/* slide 2 */
.problem .lead{position:absolute;left:9px;top:32px;width:250px;font-size:4.1px}
.card{position:absolute;top:57px;width:107px;height:75px;border-radius:7px;padding:8px 8px;color:var(--white)}
.card.blue{left:32px;background:var(--blue)}
.card.gold{left:146px;background:var(--yellow)}
.card .ico{width:17px;height:17px;border-radius:50%}
.card.blue .ico{background:var(--yellow)}
.card.gold .ico{background:var(--blue)}
.card h3{margin-top:5px;font-size:5.6px;font-weight:600;letter-spacing:.2px}
.card p{margin-top:2px;font-size:3.6px}

/* slide 3 */
.white .pitch{position:absolute;left:9px;top:35px;width:128px;font-size:5px;color:var(--ink);line-height:1.45}
.white .body{position:absolute;left:9px;top:60px;width:130px;font-size:3.8px;line-height:1.85}
.white .screen{left:154px;top:36px;width:115px;height:94px;background:linear-gradient(180deg,#2b2f36,#3d434c 60%,#cfd2d6 78%,#e6e6e6)}

/* slide 4 */
.features{position:absolute;left:9px;top:26px;width:135px}
.feat{display:flex;gap:5px;margin-bottom:6.3px}
.feat .ico{flex:0 0 16px;height:16px;border-radius:50%;border:1px solid var(--yellow);display:flex;align-items:center;justify-content:center}
.feat .ico i{width:7px;height:7px;border-radius:2px;background:var(--yellow)}
.feat h4{font-size:4.9px;font-weight:600;color:var(--blue)}
.feat p{font-size:3.4px;line-height:1.5}
.solution .photo{left:149px;top:30px;width:122px;height:108px;background:linear-gradient(150deg,#d9c4a6,#b28c63 45%,#4a5f8a 70%,#c9a47d)}

/* slide 5 */
.b2c .body{position:absolute;left:11px;top:56px;width:112px;font-size:3.9px}
.checks{position:absolute;left:9px;top:88px;width:120px;display:grid;grid-template-columns:1fr 1fr;gap:4px 6px}
.chk{display:flex;gap:2px;font-size:3.1px;line-height:1.4}
.chk b{display:block;font-weight:600;color:var(--ink)}
.chk svg{flex:0 0 4px;margin-top:.5px}
.b2c .dash{left:132px;top:53px;width:134px;height:69px;background:linear-gradient(180deg,#e9eef6,#dfe6f1 55%,#2d5da8 80%,#1f3f74);border:1px solid #c9d3e3}

/* slide 6 */
.step{position:absolute;top:37px;width:60px;height:85px;border-radius:4px;border:1px solid var(--yellow);text-align:center;padding:4px 3px 0}
.step.b{border-color:var(--blue)}
.step .num{width:21px;height:21px;margin:0 auto;border-radius:50%;background:var(--yellow);color:var(--ink);font-weight:700;font-size:7px;display:flex;align-items:center;justify-content:center}
.step.b .num{background:var(--blue);color:var(--white)}
.step h4{margin-top:5px;height:14px;display:flex;align-items:center;justify-content:center;font-size:4.3px;font-weight:600;color:var(--ink);line-height:1.3}
.step p{margin-top:3px;font-size:3.1px;line-height:1.6}
.s1{left:15px}.s2{left:80px}.s3{left:145px}.s4{left:210px}

/* slide 7 */
.about .photo{left:18px;top:28px;width:107px;height:107px;border-radius:50%;background:radial-gradient(circle at 50% 45%,#f2c94c 0,#e0b43a 18%,#c7d3dc 40%,#aeb8c0 70%,#c9a77f)}
.about .body{position:absolute;left:150px;top:49px;width:117px;font-size:3.9px;color:var(--ink)}
.about .body p+p{margin-top:3px}

/* slide 8 */
.thanks .brand{left:44px;top:31px;font-size:12px}
.thanks .brand .mark{width:7px;height:7px}
.thanks h2{position:absolute;left:44px;top:56px;font-size:8.4px;font-weight:700;color:var(--yellow);letter-spacing:.3px}
.contact{position:absolute;left:46px;top:74px;font-size:3.5px;color:var(--ink)}
.contact li{list-style:none;display:flex;gap:5px;align-items:flex-start;margin-bottom:6px;line-height:1.5}
.contact svg{flex:0 0 6px}
.contact .web{color:var(--blue)}
.thanks .rule{position:absolute;left:156px;top:0;width:2px;height:160px;background:var(--yellow)}
.thanks .photo{left:158px;top:0;width:127px;height:160px;background:linear-gradient(125deg,#3a2c22,#8a5a34 40%,#c8915a 60%,#5e86b0)}
</style>
</head>
<body>
<main class="deck">

  <section class="slide cover c1 r1">
    <div class="photo" role="img" aria-label="Photo of a mover in blue overalls carrying boxes toward a loaded van"></div>
    <div class="rule"></div>
    <div class="bg"></div>
    <div class="brand"><span class="mark"></span>Trovanta</div>
    <h1>MOVING FOR<br>THE NEXTGENERATION</h1>
    <p class="tag">From packing to tracking, we take the stress out of your moving experience.</p>
  </section>

  <section class="slide problem c2 r1">
    <span class="tab"></span>
    <div class="head"><span class="hl">THE PROBLEM</span><br>INEFFICIENCIES IN THE MOVING INDUSTRY</div>
    <div class="brand top"><span class="mark"></span>Trovanta</div>
    <p class="lead">The moving industry is plagued by middlemen van lines, brokers, and agents—who drive up costs by 15-40% without adding value. These layers result in inflated prices and poor service quality for consumers.</p>
    <div class="card blue"><div class="ico"></div><h3>TRIPLE MARGINING</h3><p>Van lines, agents, and brokers each take a cut, leaving frontline movers underpaid and service quality compromised.</p></div>
    <div class="card gold"><div class="ico"></div><h3>LACK OF ACCOUNTABILITY</h3><p>Service failures, missed deadlines, and damaged goods are commonplace due to poor communication between middlemen. The customer needs a clear party to hold accountable.</p></div>
    <div class="foot"><span>2024 © Copyrights Trovanta</span><span>Page | 02</span></div>
    <div class="bar"></div>
  </section>

  <section class="slide white c3 r1">
    <span class="tab"></span>
    <div class="head"><span class="hl">TROVANTA</span> <span class="bl">WHITE LABEL</span></div>
    <div class="brand top"><span class="mark"></span>Trovanta</div>
    <p class="pitch">Partner with Trovanta and take advantage of our cutting-edge technology to gain a competitive edge in the industry.</p>
    <p class="body">Trovanta offers a white labeling solution for companies looking to capture direct moves. Our technology platform can be customized with your branding to provide a seamless integration with your existing systems and processes. This allows you to offer a top-notch interstate moving experience to your customers, while leveraging the power of Trovanta's proven technology. With this solution, you can streamline your operations, increase customer satisfaction, and capture more business in the lucrative long-distance move market.</p>
    <div class="photo screen" role="img" aria-label="Desktop monitor showing the white-label moving website"></div>
    <div class="foot"><span>2024 © Copyrights Trovanta</span><span>Page | 03</span></div>
    <div class="bar"></div>
  </section>

  <section class="slide solution c4 r1">
    <span class="tab"></span>
    <div class="head"><span class="hl">THE SOLUTION – </span><span class="bl">TROVANTA'S AI-POWERED PLATFORM</span></div>
    <div class="brand top"><span class="mark"></span>Trovanta</div>
    <div class="features">
      <div class="feat"><div class="ico"><i></i></div><div><h4>Cutting Out Middlemen</h4><p>Trovanta directly connects customers with local movers, eliminating van lines, brokers, and agents. This streamlines the process and ensures transparent, fair pricing.</p></div></div>
      <div class="feat"><div class="ico"><i></i></div><div><h4>AI-Driven Instant Pricing</h4><p>Trovanta offers the industry's only instant, guaranteed pricing using AI, GPS, and key moving variables.</p></div></div>
      <div class="feat"><div class="ico"><i></i></div><div><h4>Automated Compliance</h4><p>Fully automates interstate regulatory compliance, reducing legal risks for all movers in the supply chain.</p></div></div>
      <div class="feat"><div class="ico"><i></i></div><div><h4>Real-Time Capacity Matching</h4><p>The platform optimizes truck capacity by matching real-time availability with customer move requests, improving operational efficiency.</p></div></div>
    </div>
    <div class="photo" role="img" aria-label="Photo of a mover in a blue cap taping a cardboard box"></div>
    <div class="foot"><span>2024 © Copyrights Trovanta</span><span>Page | 04</span></div>
    <div class="bar"></div>
  </section>

  <section class="slide b2c c1 r2">
    <span class="tab"></span>
    <div class="head"><span class="hl">B2C STRATEGY</span><span class="bl">ATTACKING B2C CONSUMER<br>MOVING MARKET</span></div>
    <div class="brand top"><span class="mark"></span>Trovanta</div>
    <p class="body">With the foundation of B2I and B2B, Trovanta will enter the B2C market with a large-scale acquisition strategy requiring significant branding &amp; credibility investment, similar to Drivello.</p>
    <div class="checks">
      <div class="chk"><svg width="4" height="4" viewBox="0 0 10 10"><path d="M1 5l3 3 5-6" fill="none" stroke="#1556d6" stroke-width="2"/></svg><span><b>Customer Acquisition Cost</b>Estimated high 4-figures to low 5-figures.</span></div>
      <div class="chk"><svg width="4" height="4" viewBox="0 0 10 10"><path d="M1 5l3 3 5-6" fill="none" stroke="#1556d6" stroke-width="2"/></svg><span><b>Gross Profit</b>Estimated $XXX.</span></div>
      <div class="chk"><svg width="4" height="4" viewBox="0 0 10 10"><path d="M1 5l3 3 5-6" fill="none" stroke="#1556d6" stroke-width="2"/></svg><span><b>Annual Moves from B2C</b>XXX moves/year.</span></div>
      <div class="chk"><svg width="4" height="4" viewBox="0 0 10 10"><path d="M1 5l3 3 5-6" fill="none" stroke="#1556d6" stroke-width="2"/></svg><span><b>EBITDA</b>Projected $XXX over the next 36 months.</span></div>
    </div>
    <div class="photo dash" role="img" aria-label="Screenshot of a market data dashboard with tables and an area chart"></div>
    <div class="foot"><span>2024 © Copyrights Trovanta</span><span>Page | 05</span></div>
    <div class="bar"></div>
  </section>

  <section class="slide checks-slide c2 r2">
    <span class="tab"></span>
    <div class="head"><span class="hl">TROVANTA</span> BUILT-IN CHECKS AND BALANCES</div>
    <div class="brand top"><span class="mark"></span>Trovanta</div>
    <div class="step s1"><div class="num">01</div><h4>INDEPENDENT<br>SURVEY COMPANY</h4><p>Trovanta automatically audits: Compliance, Insurance, Regulatory, Bonding, Background checks, and Quality.</p></div>
    <div class="step b s2"><div class="num">02</div><h4>MULTIPLE NETWORK<br>SERVICE PROVIDERS</h4><p>With several professional teams engaged there are a series of checks and cross checks.</p></div>
    <div class="step s3"><div class="num">03</div><h4>CONCIERGE SERVICE</h4><p>Proven, proactive process operated by our award-winning team of experienced customer service professionals.</p></div>
    <div class="step b s4"><div class="num">04</div><h4>IMMEDIATE CAPACITY<br>SECURED</h4><p>Virtually limitless capacity even during peak moving days.</p></div>
    <div class="foot"><span>2024 © Copyrights Trovanta</span><span>Page | 06</span></div>
    <div class="bar"></div>
  </section>

  <section class="slide about c3 r2">
    <span class="tab"></span>
    <div class="head"><span class="bl">ABOUT US</span></div>
    <div class="brand top"><span class="mark"></span>Trovanta</div>
    <div class="photo" role="img" aria-label="Photo of a happy customer stretching among moving boxes in a new home"></div>
    <div class="body">
      <p>Trovanta is the next logical evolution in professional moving. Professional moving clients have battled soaring prices, acute capacity problems and deteriorating service levels.</p>
      <p>Trovanta was founded by lifelong moving professionals who have developed the answer to better moving services. Poised as THE industry disruptor, we deliver faster, offer guaranteed prices and even offer no credit check financing options. We are a technology first organization using proprietary software to deliver moving's best service experience.</p>
    </div>
    <div class="foot"><span>2024 © Copyrights Trovanta</span><span>Page | 07</span></div>
    <div class="bar"></div>
  </section>

  <section class="slide thanks c4 r2">
    <div class="brand"><span class="mark"></span>Trovanta</div>
    <h2>THANK YOU</h2>
    <ul class="contact">
      <li><svg width="6" height="6" viewBox="0 0 12 12"><path d="M6 11S2 6.8 2 4.5a4 4 0 0 1 8 0C10 6.8 6 11 6 11z" fill="none" stroke="#1b1b1b" stroke-width="1"/><circle cx="6" cy="4.5" r="1.3" fill="none" stroke="#1b1b1b"/></svg><span>48 Harbor Lane, Suite 210,<br>Fairview, OK 73000</span></li>
      <li><svg width="6" height="6" viewBox="0 0 12 12"><path d="M3 1.5l2 2.5-1 1.3a6 6 0 0 0 2.7 2.7L8 7l2.5 2-1 1.5C5.5 10.5 1.5 6.5 1.5 2.5z" fill="none" stroke="#1b1b1b" stroke-width="1"/></svg><span>(800) 555-0142</span></li>
      <li><svg width="6" height="6" viewBox="0 0 12 12"><circle cx="6" cy="6" r="4.5" fill="none" stroke="#1b1b1b"/><path d="M1.5 6h9M6 1.5c-2.4 2.6-2.4 6.4 0 9M6 1.5c2.4 2.6 2.4 6.4 0 9" fill="none" stroke="#1b1b1b" stroke-width=".8"/></svg><span><span class="web">trovanta.example</span><br>support@trovanta.example</span></li>
    </ul>
    <div class="rule"></div>
    <div class="photo" role="img" aria-label="Photo of a hand holding a handheld scanner over packages"></div>
  </section>

</main>
</body>
</html>
```